One business card required with 2 company logos and 2 people's details

One business card required.
No preference on design - One side could show the 2 different business logos for the companies we own. The reverse could have the details shown below.
Another option could be one business one side and one business on the reverse. Happy to receive designs.

Dora Pellham
07700 913 286
Rowena Tindall
07700 958 137

website: quietmeadowbloom.co.uk
email: info@quietmeadowbloom.co.uk

website: brightharbourevents.co.uk
email: info:brightharbourevents.co.uk

May be nice to have icons instead of the words email/website?

I have included different versions of the logos to help with your design.

Contact Information for Business Card

see project overview

Requirements
Must have
• both company logos, both contact names and contact details

```html
<!DOCTYPE html>
<html lang="en">
<head>
<meta charset="utf-8">
<title>Business Card – Bright Harbour Events &amp; Quiet Meadow Bloom</title>
<link href="https://fonts.googleapis.com/css2?family=Roboto:wght@400;500;700&display=swap" rel="stylesheet">
<style>
  :root {
    --backdrop: #e9eaec;
    --card: #ffffff;
    --blue-bright: #1a8ee6;
    --blue-deep: #0a2f9e;
    --blue-mid: #0b5fd0;
    --cyan: #00bff0;
    --violet: #8f86d8;
    --navy-ink: #1c1c3a;
    --ink: #111111;
    --divider: #3b5fd6;
  }
  * { box-sizing: border-box; margin: 0; padding: 0; }
  html, body {
    width: 1200px; height: 800px; overflow: hidden;
    background: var(--backdrop);
    font-family: "Roboto", Arial, sans-serif;
  }
  .canvas {
    width: 1200px; height: 800px;
    display: flex; align-items: center; justify-content: center; gap: 40px;
  }
  .card {
    position: relative;
    width: 560px; height: 320px;
    background: var(--card);
    border-radius: 4px;
    overflow: hidden;
    box-shadow: 0 10px 30px rgba(0,0,0,0.18);
    border-bottom: 3px solid var(--blue-mid);
  }

  /* contact side */
  .wave { position: absolute; inset: 0; width: 100%; height: 100%; }
  .people {
    position: absolute; top: 24px; right: 36px;
    text-align: right;
  }
  .person + .person { margin-top: 8px; }
  .person-name {
    color: var(--blue-bright);
    font-weight: 700; font-size: 28px; line-height: 1.05;
  }
  .person-phone {
    color: var(--ink);
    font-weight: 500; font-size: 16px; line-height: 20px; letter-spacing: 0.5px;
    display: inline-flex; align-items: center; gap: 6px;
  }
  .person-phone svg { width: 13px; height: 13px; fill: var(--blue-bright); }
  .contact-list {
    position: absolute; left: 36px; bottom: 20px;
    list-style: none;
  }
  .contact-list li {
    color: #ffffff; font-size: 15px; line-height: 20px;
    display: flex; align-items: center; gap: 9px;
  }
  .contact-list svg { width: 13px; height: 13px; fill: #ffffff; flex: none; }

  /* logo side */
  .brands {
    position: absolute; inset: 0;
    display: flex; align-items: center; justify-content: center;
  }
  .brand {
    flex: 1; display: flex; align-items: center; justify-content: center; gap: 10px;
    padding: 0 20px;
  }
  .brand-dot { width: 16px; height: 16px; border-radius: 50%; flex: none; }
  .brand-name {
    font-weight: 500; font-size: 24px; line-height: 1.15; text-align: left;
  }
  .brand--events .brand-name { color: var(--blue-mid); }
  .brand--events .brand-dot { background: var(--blue-mid); }
  .brand--bloom .brand-name { color: var(--navy-ink); }
  .brand--bloom .brand-dot { background: var(--violet); }
  .brand-divider {
    width: 1px; height: 150px; background: var(--divider); opacity: 0.7;
  }
</style>
</head>
<body>
<main class="canvas">

  <section class="card card--contacts" aria-label="Contact side">
    <svg class="wave" viewBox="0 0 560 320" preserveAspectRatio="none" aria-hidden="true">
      <defs>
        <radialGradient id="waveFill" cx="0.35" cy="0.8" r="0.8">
          <stop offset="0" stop-color="#00c2f2"/>
          <stop offset="0.45" stop-color="#0b6fd6"/>
          <stop offset="1" stop-color="#0a2f9e"/>
        </radialGradient>
      </defs>
      <path d="M0,162 C150,207 380,192 560,142 L560,320 L0,320 Z" fill="#8f86d8"/>
      <path d="M0,168 C150,213 380,198 560,148 L560,320 L0,320 Z" fill="#ffffff"/>
      <path d="M0,172 C150,217 380,202 560,152 L560,320 L0,320 Z" fill="url(#waveFill)"/>
    </svg>

    <div class="people">
      <div class="person">
        <div class="person-name">Rowena Tindall</div>
        <div class="person-phone">07700 958 137
          <svg viewBox="0 0 24 24" aria-hidden="true"><path d="M6.6 10.8a15.1 15.1 0 0 0 6.6 6.6l2.2-2.2a1 1 0 0 1 1-.25 11.4 11.4 0 0 0 3.6.57 1 1 0 0 1 1 1V20a1 1 0 0 1-1 1A17 17 0 0 1 3 4a1 1 0 0 1 1-1h3.5a1 1 0 0 1 1 1c0 1.25.2 2.45.57 3.6a1 1 0 0 1-.25 1z"/></svg>
        </div>
      </div>
      <div class="person">
        <div class="person-name">Dora Pellham</div>
        <div class="person-phone">07700 913 286
          <svg viewBox="0 0 24 24" aria-hidden="true"><path d="M6.6 10.8a15.1 15.1 0 0 0 6.6 6.6l2.2-2.2a1 1 0 0 1 1-.25 11.4 11.4 0 0 0 3.6.57 1 1 0 0 1 1 1V20a1 1 0 0 1-1 1A17 17 0 0 1 3 4a1 1 0 0 1 1-1h3.5a1 1 0 0 1 1 1c0 1.25.2 2.45.57 3.6a1 1 0 0 1-.25 1z"/></svg>
        </div>
      </div>
    </div>

    <ul class="contact-list">
      <li><svg viewBox="0 0 24 24" aria-hidden="true"><path d="M2 5h20v14H2z M3 6l9 7 9-7" /></svg>info@quietmeadowbloom.co.uk</li>
      <li><svg viewBox="0 0 24 24" aria-hidden="true"><path d="M12 2a10 10 0 1 0 0 20 10 10 0 0 0 0-20zm0 2c1.2 1.6 2 3.6 2.2 6H9.8C10 7.6 10.8 5.6 12 4zm0 16c-1.2-1.6-2-3.6-2.2-6h4.4c-.2 2.4-1 4.4-2.2 6z"/></svg>www.quietmeadowbloom.co.uk</li>
      <li><svg viewBox="0 0 24 24" aria-hidden="true"><path d="M2 5h20v14H2z M3 6l9 7 9-7" /></svg>info:brightharbourevents.co.uk</li>
      <li><svg viewBox="0 0 24 24" aria-hidden="true"><path d="M12 2a10 10 0 1 0 0 20 10 10 0 0 0 0-20zm0 2c1.2 1.6 2 3.6 2.2 6H9.8C10 7.6 10.8 5.6 12 4zm0 16c-1.2-1.6-2-3.6-2.2-6h4.4c-.2 2.4-1 4.4-2.2 6z"/></svg>www.brightharbourevents.co.uk</li>
    </ul>
  </section>

  <section class="card card--brands" aria-label="Logo side">
    <div class="brands">
      <div class="brand brand--events">
        <span class="brand-dot" aria-hidden="true"></span>
        <span class="brand-name">Bright Harbour<br>Events</span>
      </div>
      <div class="brand-divider" aria-hidden="true"></div>
      <div class="brand brand--bloom">
        <span class="brand-dot" aria-hidden="true"></span>
        <span class="brand-name">Quiet Meadow<br>Bloom</span>
      </div>
    </div>
  </section>

</main>
</body>
</html>
```